I need a flyer made , the flyer can be one page or two pages or three pages . I will be posting this on Instagram and social media platforms. I am a luxury home builder , I am looking to hire a construction project manager . Below are some examples and ideas what can be on the flyer

We’re looking for a construction project manager who’s passionate about building luxury homes at the highest standards
We’re hiring construction project manager
* Experience 5+ years in residential project management with a strong portfolio of completed homes.
* location : Bergen County NJ
* excellent leadership skills, leads teams with confidence and clarity
* communicates seamlessly with architects , engineers, designers and clients
*knows how to manage budgets and timelines without compromising quality
*solves problems with a positive solution first mindset
* pays attention to every detail because in luxury the small things are the big things

Apply now , link in bio or DM to connect.

My logo is attached, my web site www.velstridebuilders.com
My style is modern but still warm and inviting. I like a clean classy look .

Please don’t add any images of chairs or people to the flyer , I do not want people on my flyer. Do not add standard images of offices and houses , we are luxury builders , we build homes over 2 million dollars. Keep a classy , simple modern look . High end .

You can add a white hard hat with my logo on it for a image , this is a suggestion does not have to be on my flyer ,

```html
<!DOCTYPE html>
<html lang="en">
<head>
<meta charset="utf-8">
<title>Velstride Builders – Hiring Carousel</title>
<link rel="stylesheet" href="https://fonts.googleapis.com/css2?family=Barlow+Condensed:ital,wght@1,800&family=Poppins:wght@300;400;500;600;700&display=swap">
<style>
  :root{
    --ink:#0b0b0b;
    --charcoal:#2a2a2a;
    --steel:#7d7d7d;
    --silver:#c4c4c4;
    --mist:#e6e6e6;
    --paper:#f7f7f7;
    --stage:#5e5e5e;
  }
  *{box-sizing:border-box;margin:0;padding:0}
  html,body{width:1200px;height:839px;overflow:hidden}
  body{background:var(--stage);font-family:"Poppins",sans-serif;color:var(--ink);
    display:flex;align-items:center;justify-content:center;gap:24px}
  .post{position:relative;width:370px;height:370px;overflow:hidden;
    background:linear-gradient(180deg,var(--paper) 0%,var(--mist) 70%,#d8d8d8 100%);
    box-shadow:0 6px 18px rgba(0,0,0,.35)}
  .deco{position:absolute;inset:0;width:100%;height:100%}
  .footer-band{position:absolute;left:0;right:0;bottom:0;height:80px;
    background:linear-gradient(180deg,rgba(0,0,0,0) 0%,rgba(0,0,0,.85) 45%,var(--ink) 70%)}
  .brand{position:absolute;left:20px;bottom:20px;display:flex;align-items:center;gap:6px;
    color:#fff;font-weight:400;font-size:13px;line-height:1;letter-spacing:.08em;text-transform:uppercase}
  .brand-dot{width:8px;height:8px;border:1px solid #fff}

  /* slide 1 */
  .hiring-eyebrow{position:absolute;left:58px;top:18px;font-weight:300;font-size:28px;line-height:1.1;color:var(--steel);letter-spacing:.02em}
  .hiring-eyebrow span{font-size:24px;margin-left:8px;letter-spacing:-3px;color:var(--charcoal)}
  .hiring-title{position:absolute;left:20px;top:44px;font-family:"Barlow Condensed",sans-serif;font-style:italic;font-weight:800;font-size:80px;line-height:1;letter-spacing:.01em}
  .role{position:absolute;left:27px;top:123px;font-size:16px;font-weight:400}
  .role-top{display:block;font-weight:400;font-size:16px;line-height:17px;color:var(--steel)}
  .role-main{display:block;font-weight:600;font-size:16.5px;line-height:18px;color:var(--charcoal)}
  .rule{position:absolute;left:0;top:170px;width:215px;height:3px;background:linear-gradient(90deg,var(--silver),#9a9a9a)}
  .intro{position:absolute;left:22px;top:196px;width:120px;font-size:10px;line-height:1.38;color:var(--ink)}

  /* slide 2 */
  .exp{position:absolute;left:164px;top:52px;display:flex;align-items:flex-end}
  .exp-num{font-weight:600;font-size:46px;line-height:.9;color:#6b6b6b}
  .exp-plus{font-weight:600;font-size:34px;line-height:1;color:var(--charcoal);margin:0 2px 2px}
  .exp-words{line-height:1}
  .exp-words b{display:block;font-weight:600;font-size:22px;color:#6b6b6b}
  .exp-words strong{display:block;font-weight:600;font-size:18px;color:var(--ink)}
  .exp-pill{position:absolute;left:102px;right:0;top:103px;height:32px;background:var(--ink);color:#fff;
    border-radius:18px 0 0 18px;font-size:9.5px;line-height:1.4;padding:3px 0 0 31px}
  .exp-rule{position:absolute;left:0;right:0;top:143px;height:5px;background:linear-gradient(90deg,var(--mist),var(--silver),#9b9b9b)}
  .checklist{position:absolute;left:20px;top:158px;list-style:none;width:240px}
  .checklist li{display:flex;gap:6px;font-size:9.5px;line-height:11.5px;margin-bottom:4.5px}
  .checklist svg{flex:none;width:10px;height:10px;margin-top:1px}

  /* slide 3 */
  .ring{position:absolute;border-radius:50%;border:4px solid #8d8d8d;padding:7px;background:rgba(255,255,255,.6)}
  .ring .photo{width:100%;height:100%;border-radius:50%}
  .apply{position:absolute;left:175px;top:227px;width:156px;height:30px;border-radius:16px;
    background:linear-gradient(180deg,#f2f2f2,#c9c9c9);border:2px solid #8a8a8a;
    font-weight:700;font-size:20px;line-height:26px;text-align:center;color:var(--ink)}
  .connect{position:absolute;left:198px;top:268px;list-style:none;font-weight:500;font-size:10.5px;line-height:1.5}
  .connect li{display:flex;align-items:center;gap:6px}
  .connect svg{width:9px;height:9px}
  .url-pill{position:absolute;right:0;bottom:28px;width:196px;height:20px;border-radius:12px 0 0 12px;
    background:linear-gradient(90deg,#3a3a3a,#6a6a6a);color:#fff;font-size:10px;line-height:20px;padding-left:18px}
</style>
</head>
<body>

<section class="post post-hiring">
  <svg class="deco" viewBox="0 0 370 370" aria-hidden="true">
    <defs>
      <linearGradient id="stripe1" x1="0" y1="0" x2="1" y2="1"><stop offset="0" stop-color="#bdbdbd"/><stop offset="1" stop-color="#6e6e6e"/></linearGradient>
    </defs>
    <polygon points="275,0 300,0 370,70 370,95" fill="url(#stripe1)"/>
    <polygon points="305,0 322,0 370,48 370,65" fill="#d6d6d6"/>
  </svg>
  <svg class="deco" viewBox="0 0 370 370" role="img" aria-label="Photo of a white luxury home exterior at dusk, framed in a sweeping arc">
    <defs>
      <linearGradient id="house" x1="0" y1="0" x2="1" y2="1"><stop offset="0" stop-color="#c9c3b6"/><stop offset=".6" stop-color="#ede7da"/><stop offset="1" stop-color="#b7ada0"/></linearGradient>
    </defs>
    <path d="M370,65 C290,70 220,150 185,300 L370,300 Z" fill="url(#house)"/>
  </svg>
  <svg class="deco" viewBox="0 0 370 370" role="img" aria-label="Photo of a white hard hat bearing the company name">
    <defs>
      <radialGradient id="hat" cx=".45" cy=".35" r=".7"><stop offset="0" stop-color="#ffffff"/><stop offset=".7" stop-color="#dcdcdc"/><stop offset="1" stop-color="#a9a9a9"/></radialGradient>
    </defs>
    <ellipse cx="272" cy="255" rx="92" ry="70" fill="url(#hat)"/>
  </svg>
  <p class="hiring-eyebrow">WE’RE<span>‹‹‹</span></p>
  <h1 class="hiring-title">HIRING</h1>
  <h2 class="role"><span class="role-top">CONSTRUCTION</span><span class="role-main">PROJECT MANAGER</span></h2>
  <div class="rule"></div>
  <p class="intro">We’re looking for a construction project manager who’s passionate about building Luxury homes at the highest standards.</p>
  <div class="footer-band"></div>
  <div class="brand"><span class="brand-dot"></span>Velstride Builders</div>
</section>

<section class="post post-requirements">
  <svg class="deco" viewBox="0 0 370 370" role="img" aria-label="Photo of a luxury home facade in soft daylight, cropped by a curve">
    <defs>
      <linearGradient id="facade" x1="0" y1="0" x2="1" y2="1"><stop offset="0" stop-color="#cdd3da"/><stop offset=".5" stop-color="#ece6da"/><stop offset="1" stop-color="#c8bca8"/></linearGradient>
    </defs>
    <path d="M0,0 L180,0 C150,20 120,70 100,130 L0,130 Z" fill="url(#facade)"/>
  </svg>
  <svg class="deco" viewBox="0 0 370 370" aria-hidden="true">
    <polygon points="272,0 300,0 370,70 370,100" fill="#9a9a9a"/>
    <polygon points="305,0 320,0 370,50 370,65" fill="#d4d4d4"/>
  </svg>
  <div class="ring" style="left:250px;top:233px;width:150px;height:150px;border-color:#b0b0b0" role="img" aria-label="Photo of a bright open-plan living room with timber floors">
    <div class="photo" style="background:linear-gradient(160deg,#f1eee8,#d8c9b0)"></div>
  </div>
  <div class="exp">
    <span class="exp-num">5</span><span class="exp-plus">+</span>
    <span class="exp-words"><b>YEARS</b><strong>EXPERIENCE</strong></span>
  </div>
  <p class="exp-pill">in Residential Project Management with<br>a Strong Portfolio of completed homes.</p>
  <div class="exp-rule"></div>
  <ul class="checklist">
    <li><svg viewBox="0 0 10 10"><circle cx="5" cy="5" r="4.4" fill="none" stroke="#111" stroke-width=".8"/><path d="M3 5.2 4.4 6.5 7 3.6" fill="none" stroke="#111" stroke-width=".9"/></svg>Location: Bergen County NJ</li>
    <li><svg viewBox="0 0 10 10"><circle cx="5" cy="5" r="4.4" fill="none" stroke="#111" stroke-width=".8"/><path d="M3 5.2 4.4 6.5 7 3.6" fill="none" stroke="#111" stroke-width=".9"/></svg>Excellent leadership skills, leads teams with confidence and clarity</li>
    <li><svg viewBox="0 0 10 10"><circle cx="5" cy="5" r="4.4" fill="none" stroke="#111" stroke-width=".8"/><path d="M3 5.2 4.4 6.5 7 3.6" fill="none" stroke="#111" stroke-width=".9"/></svg>Communicates seamlessly with architects , engineers, designers and clients</li>
    <li><svg viewBox="0 0 10 10"><circle cx="5" cy="5" r="4.4" fill="none" stroke="#111" stroke-width=".8"/><path d="M3 5.2 4.4 6.5 7 3.6" fill="none" stroke="#111" stroke-width=".9"/></svg>Knows how to manage budgets and timelines without compromising quality</li>
    <li><svg viewBox="0 0 10 10"><circle cx="5" cy="5" r="4.4" fill="none" stroke="#111" stroke-width=".8"/><path d="M3 5.2 4.4 6.5 7 3.6" fill="none" stroke="#111" stroke-width=".9"/></svg>Solves problems with a positive solution first mindset</li>
    <li><svg viewBox="0 0 10 10"><circle cx="5" cy="5" r="4.4" fill="none" stroke="#111" stroke-width=".8"/><path d="M3 5.2 4.4 6.5 7 3.6" fill="none" stroke="#111" stroke-width=".9"/></svg>Pays attention to every detail because in luxury the small things are the big things</li>
  </ul>
  <div class="footer-band" style="height:62px"></div>
  <div class="brand"><span class="brand-dot"></span>Velstride Builders</div>
</section>

<section class="post post-apply">
  <svg class="deco" viewBox="0 0 370 370" role="img" aria-label="Photo of a luxury kitchen with dark timber cabinets and stone counters">
    <defs>
      <linearGradient id="kitchen" x1="0" y1="0" x2="1" y2="1"><stop offset="0" stop-color="#5a4536"/><stop offset=".45" stop-color="#d8cfc0"/><stop offset="1" stop-color="#eeeae3"/></linearGradient>
    </defs>
    <path d="M0,0 L210,0 C215,90 150,170 40,195 L0,195 Z" fill="url(#kitchen)"/>
  </svg>
  <svg class="deco" viewBox="0 0 370 370" aria-hidden="true">
    <polygon points="272,0 300,0 370,70 370,100" fill="#9a9a9a"/>
    <polygon points="305,0 320,0 370,50 370,65" fill="#d4d4d4"/>
  </svg>
  <div class="ring" style="left:183px;top:60px;width:142px;height:142px" role="img" aria-label="Photo of a bright luxury bathroom with freestanding tub">
    <div class="photo" style="background:linear-gradient(160deg,#f2f2f0,#c9b39a)"></div>
  </div>
  <div class="ring" style="left:34px;top:183px;width:116px;height:116px" role="img" aria-label="Photo of a tiled walk-in shower in grey stone">
    <div class="photo" style="background:linear-gradient(160deg,#8e9093,#e7e7e7)"></div>
  </div>
  <p class="apply">APPLY NOW</p>
  <ul class="connect">
    <li><svg viewBox="0 0 10 10"><path d="M4 6 6 4M3 4.5 1.8 5.7a1.6 1.6 0 0 0 2.3 2.3L5.3 6.8M7 5.5 8.2 4.3A1.6 1.6 0 0 0 5.9 2L4.7 3.2" fill="none" stroke="#111" stroke-width=".9"/></svg>Link in Bio</li>
    <li><svg viewBox="0 0 10 10"><circle cx="5" cy="5" r="4.3" fill="none" stroke="#111" stroke-width=".7"/><path d="M3.7 4a1.3 1.3 0 1 1 1.8 1.2c-.4.2-.5.4-.5.8" fill="none" stroke="#111" stroke-width=".8"/><circle cx="5" cy="7.4" r=".45" fill="#111"/></svg>or DM to connect</li>
  </ul>
  <div class="footer-band" style="height:72px"></div>
  <div class="brand"><span class="brand-dot"></span>Velstride Builders</div>
  <p class="url-pill">www.velstridebuilders.com</p>
</section>

</body>
</html>
```